Voltbrisk package design alternate designs & color themes

We want to see different options from multiple artists for our Brand Voltbrisk. We are an electronic accessories company that sell everything from camera accessories to mobile device accessories. We are looking for a simple yet professional design for our packaging. Attached is one example, however we are looking for your creativity. Please use any colors / design theme that you see fit for an electronics accessory company, that blend well with the current logo.
Electronic Accessories

```html
<!DOCTYPE html>
<html lang="en">
<head>
<meta charset="UTF-8">
<title>Voltbrisk Headphone Stand Packaging</title>
<link href="https://fonts.googleapis.com/css2?family=Bebas+Neue&family=Montserrat:wght@500;700;800&display=swap" rel="stylesheet">
<style>
  :root {
    --bg: #ffffff;
    --lime: #80ff00;
    --lime-deep: #6ad900;
    --white: #ffffff;
    --ink: #262626;
    --hole: #ffffff;
  }
  * { margin: 0; padding: 0; box-sizing: border-box; }
  html, body { width: 1200px; height: 1000px; overflow: hidden; background: var(--bg); }
  .canvas { position: relative; width: 1200px; height: 1000px; }

  .pack { position: absolute; top: 40px; width: 400px; height: 920px; }
  .pack--front { left: 160px; }
  .pack--back { left: 640px; }

  .hang-tab {
    position: absolute; top: 0; left: 0; width: 100%; height: 130px;
    background: var(--lime-deep);
  }
  .hang-slot {
    position: absolute; top: 56px; left: 50%; transform: translateX(-50%);
    width: 100px; height: 30px; border-radius: 15px; background: var(--hole);
  }
  .hang-slot::before {
    content: ""; position: absolute; top: -9px; left: 50%; transform: translateX(-50%);
    width: 24px; height: 20px; border-radius: 12px 12px 0 0; background: var(--hole);
  }

  .box-face {
    position: absolute; top: 130px; left: 0; width: 100%; height: 790px;
    background: var(--lime); overflow: hidden;
  }

  .brand-band {
    position: absolute; top: 60px; height: 90px; background: var(--white);
    display: flex; align-items: center; justify-content: center;
  }
  .pack--front .brand-band { left: 0; width: 310px; border-radius: 0 45px 45px 0; }
  .pack--back .brand-band { right: 0; width: 310px; border-radius: 45px 0 0 45px; }
  .band-end {
    position: absolute; top: 60px; height: 90px; width: 70px; background: var(--white);
  }
  .pack--front .band-end { right: 0; border-radius: 45px 0 0 45px; }
  .pack--back .band-end { left: 0; border-radius: 0 45px 45px 0; }

  .brand-name {
    display: flex; align-items: center; gap: 8px;
    font-family: "Montserrat", sans-serif; font-weight: 800; font-size: 30px;
    color: var(--ink); letter-spacing: -0.5px;
  }
  .brand-dot { width: 14px; height: 14px; border-radius: 50%; background: var(--lime-deep); }

  .product-title {
    position: absolute; top: 175px; left: 0; width: 100%; text-align: center;
    font-family: "Bebas Neue", sans-serif; font-size: 44px; letter-spacing: 2px;
    color: var(--white);
  }
  .product-sub {
    position: absolute; top: 228px; left: 0; width: 100%; text-align: center;
    font-family: "Bebas Neue", sans-serif; font-size: 20px; letter-spacing: 0.5px;
    color: var(--ink);
  }

  .product-photo {
    position: absolute; top: 255px; left: 70px; width: 260px; height: 500px;
    background: linear-gradient(180deg, #3a3a3a 0%, #2a2a2a 100%);
    border-radius: 8px;
  }
  .assembly-drawing {
    position: absolute; top: 270px; left: 110px; width: 180px; height: 390px;
    border: 2px solid rgba(255,255,255,0.55); border-radius: 8px;
    background: rgba(255,255,255,0.08);
  }

  .spec-line {
    position: absolute; left: 0; width: 100%; text-align: center;
    font-family: "Bebas Neue", sans-serif; font-size: 14px; color: var(--ink);
  }
  .spec-weight { top: 672px; }
  .spec-size { top: 688px; }

  .company-block {
    position: absolute; left: 36px; top: 715px;
    font-family: "Montserrat", sans-serif; color: var(--ink); line-height: 1.25;
  }
  .company-name { font-weight: 700; font-size: 12px; }
  .company-tag { font-weight: 700; font-size: 9px; margin-bottom: 8px; }
  .company-address { font-weight: 500; font-size: 9px; }
</style>
</head>
<body>
<div class="canvas">

  <section class="pack pack--front">
    <div class="hang-tab"><div class="hang-slot"></div></div>
    <div class="box-face">
      <div class="brand-band">
        <div class="brand-name"><span class="brand-dot"></span>Voltbrisk</div>
      </div>
      <div class="band-end"></div>
      <h1 class="product-title">Headphone Stand</h1>
      <div class="product-photo" role="img" aria-label="Photo of a black aluminium headphone stand with a square base and curved top rest"></div>
    </div>
  </section>

  <section class="pack pack--back">
    <div class="hang-tab"><div class="hang-slot"></div></div>
    <div class="box-face">
      <div class="band-end"></div>
      <div class="brand-band">
        <div class="brand-name"><span class="brand-dot"></span>Voltbrisk</div>
      </div>
      <h2 class="product-title">Headphone Stand</h2>
      <p class="product-sub">High-grade alumunium</p>
      <div class="assembly-drawing" role="img" aria-label="Line drawing showing assembly of the stand: top rest, column and base joined with arrows"></div>
      <p class="spec-line spec-weight">100 G</p>
      <p class="spec-line spec-size">95 MM X 95 MM X 210 MM</p>
      <div class="company-block">
        <p class="company-name">Voltbrisk</p>
        <p class="company-tag">Electronic Accessories</p>
        <p class="company-address">Sample Address,<br>Unit #00<br>City, 12345</p>
      </div>
    </div>
  </section>

</div>
</body>
</html>
```